Create a memorable Stationary for Security Software Company

Velbrantix is the worldwide leader in securing the Internet. Making Internet communications and critical data secure, reliable and available everywhere has been and continues to be our ongoing vision. We are committed to staying focused on real customer needs and to developing new and innovative security solutions that redefine the security landscape.

Industry/Entity Type

Internet

Font styles to use
Serif
Sans Serif
Script

Colors
0792cd
33a6d7
85cae6

```html
<!DOCTYPE html>
<html lang="en">
<head>
<meta charset="utf-8">
<title>Velbrantix Business Card</title>
<link rel="stylesheet" href="https://fonts.googleapis.com/css2?family=Open+Sans:wght@400;600;700&display=swap">
<style>
  :root {
    --blue-deep: #0792cd;
    --blue-mid: #33a6d7;
    --blue-light: #85cae6;
    --ink: #000000;
    --paper: #ffffff;
    --backdrop: #ece7df;
  }
  * { margin: 0; padding: 0; box-sizing: border-box; }
  html, body {
    width: 1200px;
    height: 1119px;
    overflow: hidden;
    background: var(--backdrop);
    font-family: "Open Sans", sans-serif;
  }
  .card {
    position: absolute;
    width: 820px;
    height: 467px;
    border-radius: 20px;
    overflow: hidden;
    background: var(--ink);
    box-shadow: 0 4px 14px rgba(0,0,0,0.18);
  }
  .card-front { left: 74px; top: 53px; }
  .card-back { left: 302px; top: 570px; }
  .card-shapes { position: absolute; inset: 0; width: 100%; height: 100%; }

  .brand-name {
    position: absolute;
    color: var(--blue-mid);
    font-weight: 700;
    line-height: 1;
    white-space: nowrap;
  }
  .card-front .brand-name { left: 236px; top: 186px; transform: translate(-50%, -50%); font-size: 46px; }
  .card-back .brand-name { left: 410px; top: 240px; transform: translate(-50%, -50%); font-size: 64px; }

  .identity {
    position: absolute;
    right: 44px;
    top: 40px;
    text-align: right;
  }
  .identity-name { color: var(--paper); font-weight: 700; font-size: 29px; line-height: 1.1; }
  .identity-title { color: var(--blue-deep); font-size: 25px; line-height: 1.3; }

  .contact-list {
    position: absolute;
    right: 31px;
    top: 314px;
    list-style: none;
    color: var(--paper);
    font-size: 20px;
  }
  .contact-list li {
    display: flex;
    align-items: center;
    justify-content: flex-end;
    gap: 9px;
    height: 33.7px;
  }
  .contact-icon { width: 18px; height: 18px; fill: var(--paper); flex: none; }

  .address {
    position: absolute;
    left: 32px;
    top: 396px;
    color: var(--paper);
    font-size: 20px;
    line-height: 1.4;
    display: flex;
    gap: 9px;
  }
  .address .contact-icon { margin-top: 5px; }

  .back-url {
    position: absolute;
    left: 0;
    right: 0;
    top: 357px;
    text-align: center;
    color: var(--paper);
    font-size: 25px;
    letter-spacing: 4.5px;
  }
</style>
</head>
<body>

<section class="card card-front">
  <svg class="card-shapes" viewBox="0 0 577 329" preserveAspectRatio="none" aria-hidden="true">
    <rect width="577" height="329" fill="var(--ink)"/>
    <path d="M0,0 H346 C398,40 398,140 318,182 C230,226 90,222 0,160 Z" fill="var(--paper)"/>
    <path d="M346,0 C398,40 398,140 318,182 C230,226 90,222 0,160" fill="none" stroke="var(--blue-deep)" stroke-width="4"/>
    <path d="M338,0 C388,40 388,136 310,176 C226,216 90,212 0,152" fill="none" stroke="var(--blue-mid)" stroke-width="1"/>
    <path d="M0,180 C80,240 200,248 330,214 C430,186 500,168 577,174 V329 H0 Z" fill="var(--blue-deep)"/>
    <path d="M0,180 C80,240 200,248 330,214 C430,186 500,168 577,174" fill="none" stroke="var(--blue-light)" stroke-width="2"/>
    <path d="M0,172 C80,232 200,240 330,206 C430,178 500,160 577,166" fill="none" stroke="var(--blue-mid)" stroke-width="1.5"/>
  </svg>

  <div class="brand-name">Velbrantix</div>

  <div class="identity">
    <div class="identity-name">Your Name</div>
    <div class="identity-title">Title</div>
  </div>

  <ul class="contact-list">
    <li>
      <svg class="contact-icon" viewBox="0 0 24 24" aria-hidden="true"><path d="M6.6 10.8a15 15 0 0 0 6.6 6.6l2.2-2.2a1 1 0 0 1 1-.25 11.4 11.4 0 0 0 3.6.57 1 1 0 0 1 1 1V20a1 1 0 0 1-1 1A17 17 0 0 1 3 4a1 1 0 0 1 1-1h3.5a1 1 0 0 1 1 1 11.4 11.4 0 0 0 .57 3.6 1 1 0 0 1-.25 1z"/></svg>
      012-345-6789
    </li>
    <li>
      <svg class="contact-icon" viewBox="0 0 24 24" aria-hidden="true"><path d="M8 1h8a2 2 0 0 1 2 2v18a2 2 0 0 1-2 2H8a2 2 0 0 1-2-2V3a2 2 0 0 1 2-2zm0 3v10h8V4zm4 13a1.5 1.5 0 1 0 0 3 1.5 1.5 0 0 0 0-3z"/></svg>
      012-345-6789
    </li>
    <li>
      <svg class="contact-icon" viewBox="0 0 24 24" aria-hidden="true"><path d="M2 9l10-6 10 6v11a1 1 0 0 1-1 1H3a1 1 0 0 1-1-1zm2 1.2V19h16v-8.8l-8 5z"/></svg>
      info@velbrantix.com.com
    </li>
    <li>
      <svg class="contact-icon" viewBox="0 0 24 24" aria-hidden="true"><path d="M12 2a10 10 0 1 0 0 20 10 10 0 0 0 0-20zm6.9 9h-3a15 15 0 0 0-1.3-5.8A8 8 0 0 1 18.9 11zM12 4.1c.9 1.2 1.8 3.6 1.9 6.9h-3.8c.1-3.3 1-5.7 1.9-6.9zM9.4 5.2A15 15 0 0 0 8.1 11h-3a8 8 0 0 1 4.3-5.8zM5.1 13h3a15 15 0 0 0 1.3 5.8A8 8 0 0 1 5.1 13zm6.9 6.9c-.9-1.2-1.8-3.6-1.9-6.9h3.8c-.1 3.3-1 5.7-1.9 6.9zm2.6-1.1a15 15 0 0 0 1.3-5.8h3a8 8 0 0 1-4.3 5.8z"/></svg>
      www.velbrantix.com.com
    </li>
  </ul>

  <div class="address">
    <svg class="contact-icon" viewBox="0 0 24 24" aria-hidden="true"><path d="M12 2a7 7 0 0 0-7 7c0 5 7 13 7 13s7-8 7-13a7 7 0 0 0-7-7zm0 9.5A2.5 2.5 0 1 1 12 6.5a2.5 2.5 0 0 1 0 5z"/></svg>
    <div>Street Name, City Name<br>Zipcode-012345</div>
  </div>
</section>

<section class="card card-back">
  <div class="brand-name">Velbrantix</div>
  <div class="back-url">www.velbrantix.com.com</div>
</section>

</body>
</html>
```